Lotstallmart.com Webpage Design

Design Brief for lotstallmart.com (Copy of Brief also in attached Word file)

Name of Website- lotstallmart.com (existing logo and look & feel of website to be changed)

Logo - Finalised. The logo files are attached with the brief as “logo.jpeg”. The “Blue- Grey” version of the logo is for use on lighter backgrounds and the “Orange-White” version of the logo is for use on darker backgrounds. (A full Black version of the logo is also attached). Both versions may be used in different parts of the website. All attached files are in .png format.
Status - The website in functional and is undergoing user trials. However, we want to improve the look & feel of the website so at it seems
a. cotemporary,
b. Easy to Navigate
c. professional and
d. Vibrant.

Please visit ‘lotstallmart.com’ to check out the website and its functionalities – please use it only as a reference for the features & functions to be provided, however the designer should use a ‘Free Hand’ in designing the composition of various parts of the webpage without getting too influenced by the existing design

Objective of the Website ‘lotstallmart.com –
a. It is a portal focussed on listing of ‘Retail’ specific real-estate properties by developers, owners and realty brokers. The properties shall listed under the following four categories-
i. Retail Malls
ii. Shopping Complexes
iii. High-street shops
iv. Retail Warehouses
*refer lotstallmart.com for better clarity

b. The abovementioned properties shall be listed either for ‘Sale’ or ‘rent\lease’ or both

c. Users shall visit the site in case they wish to acquire a retail \ shop space either on ‘sale’ or ‘rent’. These Users would be able to specify the ‘Search Criteria’ through the tool-bars provided on the website – the ‘Search Criteria’ shall comprise of ‘Type of space category’, ‘City’, ‘Locality’, transaction type ie ‘Rent \ Sale’ and ‘Area Range’

d. The main revenue model for the website shall be listing fee ( or advertising charges ) payable by those listing their properties on the website.

Three Main Pages of Website (lotstallmart.com) that need to be designed -
a. Main Home Page (visit the web link - http://lotstallmart.com/ ) - The main home page has the “Search Toolbar” for specifying of Search Criteria by the User. It shall also have the following features & functions-
i. Main Advertising Banner
ii. Featured Projects
iii. New Launches
iv. Toolbar with buttons – ‘Advertise with Us’, ‘Listings Alert’, ‘Mart Wizards’, ‘Advertiser Login’

b. Property Listings Page (visit the web link - http://lotstallmart.com/gurgaon-in-india ) - The List of property options that match the Criteria specified by the ‘User’ get displayed on this page.

c. Property Detail Page - When the ‘User’ clicks on the “More….” Button on the ‘Property Listings Page’ (given in point b. above) the web page with the details of the property opens. (For Example – visit the web link - http://lotstallmart.com/vorne-Shopping-Complex-vorne-quadrion-gurgaon-636 )

Note:- Please refer to attached ‘Shopping’ related images the designer may use them on the website to provide a look & feel of retail if required – either separately or rotate in a single window

Target Market(s)

Retailers & Investors looking for retail space, Real Estate Brokers, Developers

Industry/Entity Type

Advertising

Number of Pages Required

3 page

Requirements
Must have
• Refer to existing site lotstallmart.com -- all the existing functionalities are a must have.
Nice to have
• The Designer may use the retail related images on the website if required for making it more vibrant. Refer attached images Shopping(1-6).jpg

```html
<!DOCTYPE html>
<html lang="en">
<head>
<meta charset="utf-8">
<title>Lotstallmart.com — Retail Space Portal</title>
<link rel="stylesheet" href="https://fonts.googleapis.com/css2?family=Roboto:wght@300;400;500;700&display=swap">
<style>
:root{
  --blue:#0a96ee;
  --blue-text:#1d8fe0;
  --ink:#333;
  --card:#f3f3f3;
  --nav:#2a2a2a;
  --footer:#3d3d3d;
  --footer-deep:#1c1c1c;
  --arrow:#d9412c;
}
*{box-sizing:border-box;margin:0;padding:0}
html,body{width:1200px;height:2332px;overflow:hidden}
body{font-family:"Roboto",Arial,sans-serif;color:var(--ink);background:#fff;position:relative}
.abs{position:absolute}

/* top city bar */
.city-bar{left:0;top:0;width:1200px;height:37px;background:linear-gradient(#45b8ff,#0a8fe6)}
.city-bar ul{list-style:none;position:absolute;left:174px;top:0;display:flex;height:37px}
.city-bar li{color:#fff;font-size:12px;font-weight:500;line-height:37px;padding:0 24px}
.city-bar li.active{background:#8a98a4}
.member-login{left:906px;top:7px;width:110px;height:22px;background:linear-gradient(#eee,#bbb);border-radius:3px;font-size:9px;color:#333;line-height:22px;padding-left:8px}
.member-login svg{position:absolute;right:8px;top:8px}

/* header */
.brand{left:174px;top:62px;display:flex;align-items:center;gap:8px}
.brand .dot{width:36px;height:36px;border-radius:50%;background:var(--blue)}
.brand .name{font-size:32px;font-weight:700;color:var(--blue-text);letter-spacing:-.5px}
.formats{left:466px;top:68px;display:flex}
.formats div{padding:0 18px 0 0;margin-right:18px;border-right:1px solid #ddd;font-size:11px;color:#333;line-height:16px}
.formats div:last-child{border:none}
.formats b{display:block;font-weight:400;color:var(--blue-text);font-size:12px}

/* hero */
.hero{left:0;top:137px;width:1200px;height:544px;
  background:
    radial-gradient(ellipse 320px 220px at 130px 120px,rgba(255,236,190,.55),rgba(255,236,190,0) 70%),
    radial-gradient(ellipse 320px 220px at 1060px 120px,rgba(255,236,190,.55),rgba(255,236,190,0) 70%),
    radial-gradient(ellipse 420px 300px at 600px 300px,rgba(196,120,120,.35),rgba(196,120,120,0) 70%),
    linear-gradient(180deg,#4a3a2c 0%,#8a6848 35%,#6e5038 65%,#2e2019 100%)}
.hero-arrow{top:390px}
.main-nav{left:171px;top:131px;width:858px;height:52px;background:var(--nav);display:flex;align-items:center;padding-left:22px}
.main-nav a{color:#fff;font-size:16px;text-decoration:none;padding:0 28px 0 0;margin-right:28px;border-right:1px solid #444;line-height:52px}
.main-nav a:nth-child(4){border:none}
.adv-login{left:838px;top:141px;width:177px;height:30px;background:linear-gradient(#eee,#c9c9c9);color:#333;font-size:13px;text-align:center;line-height:30px;font-weight:500}

/* search */
.search{left:172px;top:592px;width:869px;height:166px;background:var(--blue)}
.search h2{position:absolute;left:18px;top:22px;color:#fff;font-weight:400;font-size:20px}
.field{position:absolute;top:78px;width:155px}
.field label{display:block;color:#fff;font-size:14px;margin-bottom:8px}
.field .box{height:36px;background:#fff;border-radius:2px;font-size:10px;color:#777;line-height:36px;padding-left:10px;position:relative}
.field .box svg{position:absolute;right:10px;top:15px}
.search-btn{position:absolute;left:701px;top:96px;width:154px;height:39px;background:linear-gradient(#f4f4f4,#cfcfcf);color:#333;font-size:16px;text-align:center;line-height:39px;border-radius:2px}
.search-shadow{left:172px;top:758px;width:869px;height:22px;background:radial-gradient(ellipse at top,rgba(0,0,0,.18),rgba(0,0,0,0) 70%)}

/* welcome */
.welcome{left:180px;top:796px;width:840px;text-align:center}
.welcome h1{color:var(--blue-text);font-weight:500;font-size:25px;margin-bottom:14px}
.welcome p{font-size:11px;line-height:20px;color:#444}

/* featured rows */
.row-head{left:173px;font-size:19px;color:var(--blue-text);font-weight:400}
.row-head small{font-size:11px;color:#777;margin-left:4px}
.pager{left:984px;display:flex;gap:2px}
.pager span{width:20px;height:20px;background:var(--arrow);display:flex;align-items:center;justify-content:center}
.cards{left:171px;display:flex;gap:10px}
.card{width:207px;height:314px;background:var(--card);border:1px solid #e8e8e8;text-align:center;position:relative}
.card .photo{margin:7px auto 0;width:194px;height:140px;position:relative}
.card .photo::after{content:"";position:absolute;left:8px;right:8px;bottom:-14px;height:14px;background:radial-gradient(ellipse at top,rgba(0,0,0,.22),rgba(0,0,0,0) 70%)}
.photo.white{background:
  radial-gradient(ellipse 90px 50px at 60% 60%,rgba(255,255,255,.9),rgba(255,255,255,0) 70%),
  linear-gradient(180deg,#5aa3de 0%,#a9d3f2 40%,#e8ecef 62%,#8e9298 82%,#5a5e62 100%)}
.photo.tower{background:
  radial-gradient(ellipse 50px 80px at 50% 50%,rgba(226,212,200,.9),rgba(226,212,200,0) 75%),
  linear-gradient(180deg,#4e9ad6 0%,#9fcdf0 45%,#b9b2a8 70%,#5c8a4a 100%)}
.photo.red{background:
  radial-gradient(ellipse 70px 55px at 42% 58%,rgba(190,40,40,.85),rgba(190,40,40,0) 75%),
  linear-gradient(180deg,#3f8fd6 0%,#a6d2f2 40%,#e9e4dc 65%,#4d7d3c 100%)}
.photo.purple{background:
  radial-gradient(ellipse 70px 60px at 45% 55%,rgba(128,98,170,.8),rgba(128,98,170,0) 75%),
  linear-gradient(180deg,#4d98d8 0%,#b3d9f4 42%,#ece8ee 62%,#b95a3a 78%,#4e7d3d 100%)}
.photo.cream{background:
  radial-gradient(ellipse 70px 60px at 45% 55%,rgba(222,196,110,.8),rgba(222,196,110,0) 75%),
  linear-gradient(180deg,#6fb1e6 0%,#cfe6f7 42%,#efeadb 65%,#567f43 100%)}
.card h3{font-size:16px;font-weight:500;color:var(--blue-text);margin-top:26px}
.card .dev{font-size:11px;color:#555;margin-top:9px}
.card .proj{font-size:11px;color:var(--blue-text);margin-top:6px}
.card .type{font-size:11px;color:#444;font-weight:700;margin-top:6px}
.card .view{display:block;width:110px;height:29px;margin:12px auto 0;background:var(--blue);color:#fff;font-size:11px;line-height:29px}

/* bottom boxes */
.panel{top:1719px;height:267px;background:var(--card);border:1px solid #e8e8e8}
.panel h4{font-size:20px;font-weight:400;color:var(--blue-text)}
.panel p{font-size:11.5px;line-height:19px;color:#444}
.input{height:32px;background:#fff;border:1px solid #ddd;font-size:10px;color:#888;line-height:32px;padding-left:12px}
.btn{height:28px;background:var(--blue);color:#fff;font-size:10px;text-align:center;line-height:28px}
.alert{left:174px;width:280px}
.editor{left:469px;width:282px}
.wizards{left:757px;width:272px;background:var(--blue);border-color:var(--blue)}
.wizards h4,.wizards p{color:#fff}
.wizards .input{border-color:#fff}
.wizards .btn{background:linear-gradient(#f4f4f4,#cfcfcf);color:#333}

/* footer */
.footer{left:0;top:2023px;width:1200px;height:246px;background:var(--footer)}
.footer h5{position:absolute;top:32px;color:#fff;font-size:12.5px;font-weight:500}
.footer ul{list-style:none;position:absolute;top:76px}
.footer li{color:#fff;font-size:11.5px;line-height:20px}
.footer li::before{content:"▸";font-size:8px;margin-right:8px;vertical-align:1px}
.footer .about{position:absolute;left:463px;top:67px;width:325px;font-size:11px;line-height:20.5px;color:#fff}
.footer .divider{position:absolute;top:0;width:1px;height:246px;background:#333}
.contact{position:absolute;left:849px;color:#fff;font-size:12px;line-height:20px}
.contact svg{position:absolute;left:0;top:3px}
.contact div{padding-left:26px}
.bottom-bar{left:0;top:2269px;width:1200px;height:63px;background:var(--footer-deep)}
.bottom-bar p{position:absolute;left:174px;top:24px;color:#888;font-size:10.5px}
.social{position:absolute;left:888px;top:15px;display:flex;gap:9px}
.social span{width:30px;height:30px;border-radius:50%;background:#4a4a4a;box-shadow:inset 0 1px 0 rgba(255,255,255,.12)}
.bottom-bar .code{position:absolute;left:1124px;top:24px;color:#888;font-size:10.5px}
</style>
</head>
<body>

<div class="abs city-bar">
  <ul>
    <li class="active">NOIDA</li><li>DELHI</li><li>MUMBAI</li><li>CHENNAI</li><li>BANGALORE</li><li>PUNE</li><li>MORE</li>
  </ul>
</div>
<div class="abs member-login">MEMBER LOGIN
  <svg width="8" height="6"><path d="M0 0h8L4 6z" fill="#333"/></svg>
</div>

<div class="abs brand"><span class="dot"></span><span class="name">lotstallmart</span></div>
<div class="abs formats">
  <div><b>Retail Malls</b>Centrally Air-Conditioned</div>
  <div><b>Shopping Complex</b>Centrally Air-Conditioned</div>
  <div><b>High Street Shops Malls</b>Centrally Air-Conditioned</div>
  <div><b>Retail Warehouses</b>Centrally Air-Conditioned</div>
</div>

<div class="abs hero" role="img" aria-label="Family walking with shopping bags through a festively lit retail arcade"></div>
<svg class="abs hero-arrow" style="left:38px" width="20" height="24"><path d="M14 3L5 12l9 9" stroke="#fff" stroke-width="2.5" fill="none" opacity=".8"/></svg>
<svg class="abs hero-arrow" style="left:1140px" width="20" height="24"><path d="M6 3l9 9-9 9" stroke="#fff" stroke-width="2.5" fill="none" opacity=".8"/></svg>

<nav class="abs main-nav">
  <a>Home</a><a>Advertise with us</a><a>Mart Wizards</a><a>Listing Alert</a>
</nav>
<div class="abs adv-login">ADVERTISER LOGIN</div>

<section class="abs search">
  <h2>SELECT RETAIL FORMAT</h2>
  <div class="field" style="left:18px"><label>Sale Or Rent Or Both:</label><div class="box">Enter Your Name<svg width="8" height="6"><path d="M0 0h8L4 6z" fill="#333"/></svg></div></div>
  <div class="field" style="left:188px"><label>Select City:</label><div class="box">--Select--<svg width="8" height="6"><path d="M0 0h8L4 6z" fill="#333"/></svg></div></div>
  <div class="field" style="left:359px"><label>Select Locality</label><div class="box">--Select--<svg width="8" height="6"><path d="M0 0h8L4 6z" fill="#333"/></svg></div></div>
  <div class="field" style="left:530px"><label>Enter Keywords:</label><div class="box">Enter Your keywords<svg width="8" height="6"><path d="M0 0h8L4 6z" fill="#333"/></svg></div></div>
  <div class="search-btn">SEARCH</div>
</section>
<div class="abs search-shadow"></div>

<section class="abs welcome">
  <h1>Welcome To Lotstallmart.com</h1>
  <p>Lorem ipsum dolor sit amet, consectetur adipiscing elit, sed do eiusmod tempor incididunt ut labore et dolore magna aliqua. Ut enim ad minim veniam, quis nostrud exercitation ullamco laboris nisi ut aliquip ex ea commodo consequat. Duis aute irure dolor in reprehenderit in voluptate velit esse cillum dolore eu fugiat nulla pariatur. Excepteur sint occaecat cupidatat non proident, sunt in culpa qui officia deserunt mollit anim id est laborum reprehenderit in voluptate velit esse cillum dolore eu fugiat nulla pariatur. Excepteur sint occaecat cupidatat non proident, sunt in culpa qui officia</p>
</section>

<h2 class="abs row-head" style="top:957px">Featured Retail Projects<small>Across India</small></h2>
<div class="abs pager" style="top:961px">
  <span><svg width="6" height="9"><path d="M5 1L1 4.5 5 8" stroke="#fff" fill="none"/></svg></span>
  <span><svg width="6" height="9"><path d="M1 1l4 3.5L1 8" stroke="#fff" fill="none"/></svg></span>
</div>
<div class="abs cards" style="top:995px">
  <article class="card"><div class="photo white" role="img" aria-label="Modern white two-storey retail building"></div><h3>FARIDABAD</h3><div class="dev">Corvell</div><div class="proj">Ardent</div><div class="type">Shopping Complex</div><span class="view">View the listing</span></article>
  <article class="card"><div class="photo tower" role="img" aria-label="Tall high-rise tower against blue sky"></div><h3>NEW DELHI</h3><div class="dev">Corvell</div><div class="proj">Ardent</div><div class="type">Shopping Complex</div><span class="view">View the listing</span></article>
  <article class="card"><div class="photo red" role="img" aria-label="Red and white complex building"></div><h3>SURAT</h3><div class="dev">Corvell</div><div class="proj">Ardent</div><div class="type">Shopping Complex</div><span class="view">View the listing</span></article>
  <article class="card"><div class="photo purple" role="img" aria-label="Purple and white apartment block"></div><h3>GURGAON</h3><div class="dev">Corvell</div><div class="proj">Ardent</div><div class="type">Shopping Complex</div><span class="view">View the listing</span></article>
</div>

<h2 class="abs row-head" style="top:1339px">Featured New Launches<small>Across India</small></h2>
<div class="abs pager" style="top:1344px">
  <span><svg width="6" height="9"><path d="M5 1L1 4.5 5 8" stroke="#fff" fill="none"/></svg></span>
  <span><svg width="6" height="9"><path d="M1 1l4 3.5L1 8" stroke="#fff" fill="none"/></svg></span>
</div>
<div class="abs cards" style="top:1377px">
  <article class="card"><div class="photo cream" role="img" aria-label="Cream and yellow apartment block"></div><h3>FARIDABAD</h3><div class="dev">Corvell</div><div class="proj">Ardent</div><div class="type">Shopping Complex</div><span class="view">View the listing</span></article>
  <article class="card"><div class="photo red" role="img" aria-label="Red and white complex building"></div><h3>BANGALORE</h3><div class="dev">Corvell</div><div class="proj">Ardent</div><div class="type">Shopping Complex</div><span class="view">View the listing</span></article>
  <article class="card"><div class="photo white" role="img" aria-label="Modern white two-storey retail building"></div><h3>MOHALI</h3><div class="dev">Corvell</div><div class="proj">Ardent</div><div class="type">Shopping Complex</div><span class="view">View the listing</span></article>
  <article class="card"><div class="photo purple" role="img" aria-label="Purple and white apartment block"></div><h3>BHOPAL</h3><div class="dev">Corvell</div><div class="proj">Ardent</div><div class="type">Shopping Complex</div><span class="view">View the listing</span></article>
</div>

<section class="abs panel alert">
  <svg class="abs" style="left:36px;top:16px" width="30" height="22"><rect x="1" y="1" width="28" height="20" fill="none" stroke="#aaa" stroke-width="1.5"/><path d="M1 1l14 11L29 1" fill="none" stroke="#aaa" stroke-width="1.5"/></svg>
  <h4 class="abs" style="left:80px;top:14px">Listing Alert</h4>
  <p class="abs" style="left:36px;top:50px;width:225px;font-size:11px">Suscribe for Fortnightly Email update on New Listings @ Lotstallmart</p>
  <div class="abs input" style="left:32px;top:97px;width:228px">Enter Your Name:</div>
  <div class="abs input" style="left:32px;top:139px;width:228px">Enter Your Email:</div>
  <div class="abs btn" style="left:168px;top:196px;width:91px">Submit</div>
</section>

<section class="abs panel editor">
  <h4 class="abs" style="left:11px;top:12px">Editor's Choice</h4>
  <p class="abs" style="left:11px;top:42px;width:262px;font-size:11px;line-height:20px">A "Select" Listing of Retail Properties Handpicked by our Editors based on their own positive evaluation on parameters &amp; attributes such as Design Concept, Location, Developer, Success Potential. So Read On to Check Out for yourself ............ ..</p>
  <div class="abs btn" style="left:191px;top:198px;width:70px">More...</div>
</section>

<section class="abs panel wizards">
  <h4 class="abs" style="left:16px;top:12px">Mart Wizards</h4>
  <p class="abs" style="left:20px;top:48px;width:240px;font-size:11px">Post your Retail Space requirement with us and our experts shall get back</p>
  <div class="abs input" style="left:17px;top:96px;width:230px">Enter Your Email Address:</div>
  <div class="abs input" style="left:17px;top:139px;width:230px">Mobile:</div>
  <div class="abs btn" style="left:157px;top:196px;width:90px">Submit</div>
</section>

<footer class="abs footer">
  <span class="divider" style="left:438px"></span>
  <span class="divider" style="left:798px"></span>
  <h5 style="left:180px">ABOUT MARKET HUB</h5>
  <ul style="left:182px"><li>About Us</li><li>Privacy Police</li><li>Terms of Use</li><li>Contact Us</li><li>Site Map</li></ul>
  <ul style="left:308px"><li>Retail Malls</li><li>Shopping Complex</li><li>High Street Shops</li><li>Retail Warehouses</li></ul>
  <h5 style="left:463px">WWW.LOTSTALLMART.COM</h5>
  <p class="about">Lotstallmart.com - About Us Lotstallmart.com is a Specialised Web based platform for Retail Space, featuring properties across India under various formats such as Retail Malls, Shopping Complexes, High-street Shops. Also featured are Retail Warehouses which provide the logistic back-end for the retail business. Lotstallmart.com is useful to various category of users as follows- a.</p>
  <h5 style="left:849px">CONTACTS</h5>
  <div class="contact" style="top:68px">
    <svg width="12" height="16"><path d="M6 0a6 6 0 0 0-6 6c0 4.5 6 10 6 10s6-5.5 6-10a6 6 0 0 0-6-6z" fill="#fff"/><circle cx="6" cy="6" r="2.2" fill="#3d3d3d"/></svg>
    <div>Market Hub,<br>Unit 218, 2nd Floor,<br>P. O BOX 41870, Arlow.</div>
  </div>
  <div class="contact" style="top:144px">
    <svg width="13" height="13"><path d="M3 0l3 3-2 2c1 2 2 3 4 4l2-2 3 3-2 3C6 13 0 7 0 3z" fill="#fff"/></svg>
    <div>+000 555 014 2271</div>
  </div>
  <div class="contact" style="top:172px">
    <svg width="13" height="10"><path d="M0 0h13v10H0z" fill="#fff"/><path d="M0 0l6.5 5L13 0" fill="none" stroke="#3d3d3d"/></svg>
    <div>Lotstallmart.com</div>
  </div>
</footer>

<div class="abs bottom-bar">
  <p>All Rights Reserved. Copyrights @ 2015</p>
  <div class="social"><span></span><span></span><span></span><span></span></div>
  <span class="code">D2</span>
</div>

</body>
</html>
```